L.U.M Ventures - Business Card

We need a business card design for a new company based in Malaysia, called L.U.M Ventures Sdn. Bhd. We create, develop & customize database & software/web-based business systems to suit our clients need, mainly in oil&gas industry.

We would like to challenge the creativity of you to design a simple, meaningful, modern, professional & sleek. The design concept may varies but worthy enough for the recipients to proudly keep it in their wallet, and award us with fruitful business opportunities.

B-3-12 Orchid Plaza,
JK9/4, Taman Melur,
43210 Selangor. Malaysia

http://lumventures-example.com

HAFIZ Kamaru | +6012-3817720 | Co-Founder
Ed Suhaimi | +6012-4093381 | Co-Founder
Abdul Nizam | +6019-5268149 | Managing Director

Target Market(s)

The target market will expand to several other industries such as aviation, communication, automotive, education & hotel.

Industry/Entity Type

Business

Font styles to use
Serif
Sans Serif
Decorative
Script

Requirements
Must have
• plain background yet colourful concept.
Should not have
• something too easy that I can draw myself

```html
<!DOCTYPE html>
<html lang="en">
<head>
<meta charset="utf-8">
<title>L.U.M Ventures - Business Card</title>
<link rel="stylesheet" href="https://fonts.googleapis.com/css2?family=Lato:wght@400;700&display=swap">
<style>
  :root {
    --page-bg: #a9a9a9;
    --card-bg: #050505;
    --name-green: #8dc63f;
    --text-white: #ffffff;
    --contact-pink: #e84f6b;
    --address-teal: #1f8c8e;
    --art-green: #2f9a68;
    --art-yellow: #8f8a36;
    --art-pink: #9a2f62;
  }
  * { margin: 0; padding: 0; box-sizing: border-box; }
  html, body {
    width: 1200px;
    height: 900px;
    overflow: hidden;
    background: var(--page-bg);
    font-family: "Lato", Arial, sans-serif;
  }
  .business-card {
    position: absolute;
    left: 100px;
    top: 164px;
    width: 1000px;
    height: 571px;
    border-radius: 26px;
    background: var(--card-bg);
    overflow: hidden;
  }
  .card-artwork {
    position: absolute;
    left: 0;
    top: 0;
    width: 680px;
    height: 100%;
    background:
      linear-gradient(90deg, rgba(5,5,5,0) 0%, rgba(5,5,5,0) 55%, var(--card-bg) 100%),
      linear-gradient(200deg, var(--art-pink) 0%, var(--art-yellow) 45%, var(--art-green) 80%);
  }
  .card-details {
    position: absolute;
    right: 62px;
    top: 178px;
    text-align: right;
    color: var(--text-white);
  }
  .person-name {
    font-size: 48px;
    line-height: 1;
    color: var(--name-green);
    font-weight: 400;
  }
  .person-name strong { font-weight: 700; }
  .person-role {
    font-size: 23px;
    font-weight: 400;
    margin-top: 6px;
  }
  .contact-list {
    margin-top: 42px;
    display: flex;
    flex-direction: column;
    align-items: flex-end;
    gap: 8px;
  }
  .contact-item {
    display: inline-block;
    background: var(--contact-pink);
    font-size: 30px;
    line-height: 38px;
    padding: 0 8px;
    white-space: nowrap;
  }
  .address-list {
    margin-top: 40px;
    display: flex;
    flex-direction: column;
    align-items: flex-end;
    gap: 8px;
    font-style: normal;
  }
  .address-line {
    display: inline-block;
    background: var(--address-teal);
    font-size: 21px;
    line-height: 28px;
    padding: 0 8px;
    white-space: nowrap;
  }
</style>
</head>
<body>
  <div class="business-card">
    <div class="card-artwork" role="img" aria-label="Abstract artwork of glowing light streaks in green, yellow and pink"></div>

    <div class="card-details">
      <h1 class="person-name">Ed <strong>Suhaimi</strong></h1>
      <p class="person-role">Co-Founder</p>

      <div class="contact-list">
        <span class="contact-item contact-phone">+6012-4093381</span>
        <span class="contact-item contact-web">http://lumventures-example.com</span>
      </div>

      <address class="address-list">
        <span class="address-line">B-3-12 Orchid Plaza</span>
        <span class="address-line">JK9/4, Taman Melur</span>
        <span class="address-line">43210 Selangor. Malaysia</span>
      </address>
    </div>
  </div>
</body>
</html>
```